Printer Cartridges Supplier Namecard

Attached is my company logo and the design of my current namecard. I would like to have a more special look for it. Can have a little cuteness too rather than those normal standard feel. I'm a supplier mainly dealing with original and compatible printer toner cartridges, some other products like paper supplies as well.

Target Market(s)

Companies, businesses, corporates

Industry/Entity Type

It Company

Contact Information for Business Card

Logo, name, contact, address, supplies and maybe a slogan

Colors
85cae6
33a6d7
3176b5
0255a3
0792cd
85abd2

Requirements
Must have
• Logo, name, contact and address basic details.
• Must include some pictures, not just rearrange what I'm currently having.
Nice to have
• Be creative and bold, a diiferent traditional feel.

```html
<!DOCTYPE html>
<html lang="en">
<head>
<meta charset="utf-8">
<title>Tonero Namecard</title>
<link rel="stylesheet" href="https://fonts.googleapis.com/css2?family=Open+Sans:wght@400;600;700&display=swap">
<style>
  :root {
    --stage: #898a8e;
    --card-light: #f3f3f3;
    --card-blue: #62b5e5;
    --ink-grey: #58595b;
    --ink-dark: #222222;
    --accent-blue: #29abe2;
    --white: #ffffff;
  }
  * { margin: 0; padding: 0; box-sizing: border-box; }
  html, body {
    width: 1200px; height: 900px; overflow: hidden;
    background: var(--stage);
    font-family: "Open Sans", Arial, sans-serif;
  }
  .canvas { position: relative; width: 1200px; height: 900px; }
  .card {
    position: absolute; top: 184px;
    width: 302px; height: 491px;
    border-radius: 14px;
  }
  .card--front { left: 298px; background: var(--card-light); text-align: center; }
  .card--back { left: 646px; background: var(--card-blue); color: var(--white); }

  .brand-name {
    position: absolute; left: 0; right: 0; top: 80px;
    font-size: 50px; font-weight: 400; color: var(--ink-grey);
    letter-spacing: 0.5px;
  }
  .person { position: absolute; left: 0; right: 0; top: 226px; }
  .person__name { font-size: 22px; font-weight: 700; color: var(--ink-grey); line-height: 1.2; }
  .person__name .surname { color: var(--accent-blue); }
  .person__role { font-size: 13px; color: var(--ink-dark); margin-top: 2px; }
  .contacts { margin-top: 24px; font-size: 14px; color: var(--ink-dark); line-height: 19px; }
  .contacts .label { color: var(--accent-blue); font-weight: 600; }
  .address { margin-top: 22px; font-size: 15px; color: var(--ink-dark); line-height: 19px; }

  .services { position: absolute; left: 38px; top: 118px; list-style: none; }
  .services li {
    display: flex; align-items: center;
    font-size: 17px; font-weight: 700; height: 33px;
  }
  .services li::before {
    content: ""; width: 12px; height: 12px; margin-right: 14px;
    background: var(--white); transform: rotate(45deg);
  }
  .lockup { position: absolute; left: 26px; top: 312px; display: flex; align-items: center; gap: 12px; }
  .lockup__mark { width: 56px; height: 56px; background: var(--white); border-radius: 8px; }
  .lockup__name { font-size: 46px; font-weight: 400; color: var(--white); line-height: 1; }
  .tagline {
    position: absolute; left: 96px; top: 364px;
    font-size: 8px; font-weight: 600; color: var(--white);
  }
</style>
</head>
<body>
<main class="canvas">
  <section class="card card--front">
    <div class="brand-name">tonero.sg</div>
    <div class="person">
      <div class="person__name">Elina <span class="surname">Tanaka</span></div>
      <div class="person__role">Sales Executive</div>
      <div class="contacts">
        <div><span class="label">P</span>: 9000 4817</div>
        <div><span class="label">E</span>: elina@tonero.sg</div>
        <div><span class="label">W</span>: www.tonero.sg</div>
      </div>
      <div class="address">
        <div>114A Harbourview Crescent</div>
        <div>#05-210</div>
        <div>Singapore 500114</div>
      </div>
    </div>
  </section>

  <section class="card card--back">
    <ul class="services">
      <li>Printer Ink &amp; Toner Catridge</li>
      <li>Orginal Printer Catridge</li>
      <li>Paper Product</li>
      <li>Printer Maintance &amp; Repair</li>
    </ul>
    <div class="lockup">
      <span class="lockup__mark"></span>
      <span class="lockup__name">tonero.sg</span>
    </div>
    <div class="tagline">Compatible printer ink and toner solutions</div>
  </section>
</main>
</body>
</html>
```